Need Business Card for our Real Estate Business with Sales Executive's Picture

PANTONE 484 C ( RED)

PANTONE 2766 C ( BLUE

Industry/Entity Type

Real Estate

Contact Information for Business Card

Name, Mobile, email, & picture of Person
Agency Phone, address, Web address

Requirements
Must have
• Our Logo Colours, Agent Picture,

```html
<!DOCTYPE html>
<html lang="en">
<head>
<meta charset="utf-8">
<title>Marlow Homes – Business Card</title>
<link rel="stylesheet" href="https://fonts.googleapis.com/css2?family=Work+Sans:wght@400;600;700&display=swap">
<style>
  :root {
    --navy: #0c1a45;
    --red: #7a1420;
    --white: #ffffff;
    --grey: #5a5f6b;
    --backdrop: #3a3a3c;
  }
  * { margin: 0; padding: 0; box-sizing: border-box; }
  html, body { width: 1200px; height: 900px; overflow: hidden; }
  body {
    background: var(--backdrop);
    font-family: "Work Sans", Arial, sans-serif;
    position: relative;
  }
  .card {
    position: absolute;
    width: 640px;
    height: 366px;
    background: var(--white);
    border-radius: 22px;
    overflow: hidden;
  }
  .card--front { left: 500px; top: 50px; }
  .card--back  { left: 60px;  top: 480px; }

  .portrait {
    position: absolute;
    left: 0; top: 40px;
    width: 300px; height: 326px;
    background: linear-gradient(160deg, #2c3f8f 0%, #1e2d6e 60%, #141f52 100%);
  }
  .brand {
    position: absolute;
    display: flex;
    align-items: center;
    gap: 10px;
    color: var(--navy);
    font-weight: 600;
    letter-spacing: 2px;
    text-transform: uppercase;
    white-space: nowrap;
    line-height: 1;
  }
  .brand__mark { width: 12px; height: 12px; background: var(--red); }
  .card--front .brand { left: 340px; top: 165px; font-size: 26px; }
  .brand-rule {
    position: absolute;
    height: 2px;
    background: var(--navy);
  }
  .card--front .brand-rule { left: 340px; top: 210px; width: 260px; }

  .waves { position: absolute; inset: 0; }
  .card--back .brand { left: 40px; top: 100px; font-size: 26px; }
  .card--back .brand-rule { left: 40px; top: 142px; width: 300px; }

  .contacts {
    position: absolute;
    left: 40px; top: 156px;
    list-style: none;
    font-size: 15px;
    color: var(--grey);
    line-height: 24px;
  }
  .contacts li { display: flex; align-items: center; gap: 10px; }
  .contacts svg { width: 12px; height: 12px; fill: var(--grey); }

  .person {
    position: absolute;
    right: 44px; top: 234px;
    text-align: right;
    line-height: 1.2;
  }
  .person__name { font-size: 26px; font-weight: 700; color: var(--navy); letter-spacing: 1px; }
  .person__role { font-size: 17px; color: var(--grey); letter-spacing: 1px; }
  .person-rule {
    position: absolute;
    left: 40px; top: 274px;
    width: 320px; height: 2px;
    background: var(--navy);
  }
  .side-bars { position: absolute; right: 0; top: 238px; display: flex; gap: 4px; }
  .side-bars span { width: 6px; height: 52px; background: var(--red); }
  .side-bars span + span { width: 18px; background: var(--navy); }

  .address {
    position: absolute;
    right: 44px; top: 302px;
    text-align: right;
    font-size: 17px;
    font-style: normal;
    color: var(--grey);
    line-height: 24px;
  }
</style>
</head>
<body>

  <section class="card card--front">
    <div class="portrait" role="img" aria-label="Photo of the sales executive in a navy suit and striped tie"></div>
    <div class="brand"><span class="brand__mark"></span>Marlow Homes</div>
    <div class="brand-rule"></div>
  </section>

  <section class="card card--back">
    <svg class="waves" viewBox="0 0 640 366" preserveAspectRatio="none" aria-hidden="true">
      <path d="M0,0 H640 V222 C520,216 470,146 380,96 C300,52 200,44 0,44 Z" fill="#7a1420"/>
      <path d="M0,0 H640 V214 C520,208 470,138 380,88 C300,44 200,36 0,36 Z" fill="#ffffff"/>
      <path d="M0,0 H640 V206 C520,200 470,130 380,80 C300,36 200,28 0,28 Z" fill="#0c1a45"/>
      <path d="M0,0 H180 C120,8 60,12 0,12 Z" fill="#7a1420"/>
    </svg>

    <div class="brand"><span class="brand__mark"></span>Marlow Homes</div>
    <div class="brand-rule"></div>

    <ul class="contacts">
      <li><svg viewBox="0 0 12 12"><path d="M2 1l2 0 1 3-1.5 1a7 7 0 0 0 3.5 3.5L8 7l3 1v2a1 1 0 0 1-1 1A9 9 0 0 1 1 2a1 1 0 0 1 1-1z"/></svg>+852 2190 4417</li>
      <li><svg viewBox="0 0 12 12"><rect x="1" y="4" width="10" height="7" rx="1"/><rect x="3" y="1" width="6" height="3"/></svg>+852 2190 4482</li>
      <li><svg viewBox="0 0 12 12"><path d="M1 2h10v8H1z M1 2l5 4 5-4" fill="none" stroke="#5a5f6b" stroke-width="1.2"/></svg>hello@marlowhomes.com</li>
      <li><svg viewBox="0 0 12 12"><circle cx="6" cy="6" r="5" fill="none" stroke="#5a5f6b" stroke-width="1.2"/><path d="M1 6h10M6 1v10" stroke="#5a5f6b" stroke-width="1"/></svg>www.marlowhomes.com</li>
    </ul>

    <div class="person-rule"></div>
    <div class="person">
      <div class="person__name">DANIEL REYES</div>
      <div class="person__role">Managing Director</div>
    </div>
    <div class="side-bars"><span></span><span></span></div>

    <address class="address">
      Via Roma Nuova,<br>148. 12030 Saluzzo (CN)
    </address>
  </section>

</body>
</html>
```